Travel Agency Website - Simple General

Need a 7 page simple design that is pretty repetitive. Need to be able to load quickly that is SEO optimized. Trying to give ideas on what they can do, be personal as we are local, but at the same time come across as professional and get information easily with little burden.

- Landing Page
- Brimwell Vacations Page
- Family Trips
- Road Trips from Texas
- Other Destinations
- About Us Page
- Contact Us Page

Target Market(s)

Families

Coding

Coded - Design and coding required

Number of Pages Required

5+ page

Colors

Designer to choose colors to be used in the design.

Requirements
Must have
• Like it to flow easily with our logo. Use that for colors, etc.

```html
<!DOCTYPE html>
<html lang="en">
<head>
<meta charset="utf-8">
<title>Meadowlark Travel Co. – Plan Your Perfect Family Adventure</title>
<link rel="stylesheet" href="https://fonts.googleapis.com/css2?family=Barlow+Condensed:wght@500;600&family=Outfit:wght@400;500;600&display=swap">
<style>
  :root{
    --bg:#eceee6;
    --ink:#0e3a4c;
    --teal:#16807a;
    --gold:#c4954a;
    --card:#eef0ea;
    --tag:#c9d1cf;
    --muted:#2f4b57;
  }
  *{box-sizing:border-box;margin:0;padding:0}
  html,body{width:1200px;height:826px;overflow:hidden}
  body{background:var(--bg);font-family:"Outfit",sans-serif;color:var(--ink);position:relative}
  .hero-backdrop{position:absolute;inset:0;
    background:
      radial-gradient(ellipse 380px 520px at 1080px 480px, rgba(176,150,110,.55), rgba(236,238,230,0) 70%),
      radial-gradient(ellipse 160px 90px at 440px 235px, rgba(190,160,150,.22), rgba(236,238,230,0) 70%),
      var(--bg);}
  .site-header{position:absolute;left:125px;right:125px;top:19px;height:82px;display:flex;align-items:center;justify-content:space-between}
  .brand{display:flex;align-items:center;gap:8px;font-family:"Outfit",sans-serif;font-weight:600;font-size:15px;color:var(--ink);line-height:1.1;width:130px}
  .brand-dot{width:14px;height:14px;border-radius:50%;background:var(--teal);flex:none}
  .main-nav{display:flex;gap:24px;font-size:10.6px;margin-top:-10px}
  .main-nav a{color:var(--ink);text-decoration:none}
  .headline{position:absolute;top:172px;left:0;right:0;text-align:center;font-family:"Barlow Condensed",sans-serif;font-weight:600;font-size:58px;letter-spacing:-.5px;color:var(--ink)}
  .headline em{font-style:normal;color:var(--teal)}
  .tagline{position:absolute;top:254px;left:0;right:0;text-align:center;font-size:14px;color:var(--ink)}
  .tagline span.sep{margin:0 9px;font-size:9px;vertical-align:2px}
  .cards{position:absolute;top:316px;left:129px;display:flex;gap:10px}
  .card{width:229px;height:326px;background:var(--card);border-radius:14px;position:relative;overflow:hidden;box-shadow:0 6px 18px rgba(40,60,60,.08)}
  .card-photo{position:absolute;left:5px;right:5px;top:5px;height:210px;border-radius:10px 10px 0 0;-webkit-mask-image:linear-gradient(#000 60%,transparent);mask-image:linear-gradient(#000 60%,transparent)}
  .p1{background:linear-gradient(160deg,#b8a17f,#5f8fa3 45%,#7a5a4a)}
  .p2{background:linear-gradient(160deg,#c9c2b8,#8a7e74 50%,#b69a82)}
  .p3{background:linear-gradient(160deg,#8ea36f,#c7b8a0 45%,#6c86a0)}
  .p4{background:linear-gradient(160deg,#3f6a3a,#6f8e4c 50%,#d8d2c4)}
  .card-title{position:absolute;left:29px;top:195px;font-family:"Barlow Condensed",sans-serif;font-weight:500;font-size:20px;line-height:22px;color:var(--ink)}
  .card-text{position:absolute;left:29px;top:245px;font-size:9.4px;color:var(--muted)}
  .tags{position:absolute;left:29px;top:272px;display:flex;gap:2px}
  .tag{background:var(--tag);border-radius:9px;padding:0 12px;height:17px;line-height:17px;font-family:"Barlow Condensed",sans-serif;font-weight:600;font-size:7px;color:var(--ink)}
  .contact-bar{position:absolute;top:723px;left:239px;display:flex;align-items:center}
  .contact-item{display:flex;align-items:center;gap:11px}
  .icon-circle{width:48px;height:48px;border-radius:50%;background:var(--gold);display:flex;align-items:center;justify-content:center}
  .icon-circle.small{width:26px;height:26px}
  .contact-label{font-weight:600;font-size:10px}
  .contact-value{font-size:13px;margin-top:2px}
  .social{font-size:10.6px;color:var(--ink);text-decoration:underline;font-weight:500}
</style>
</head>
<body>
  <div class="hero-backdrop" role="img" aria-label="Soft backdrop photo of a traveler with a backpack overlooking a view and a plane in the sky"></div>

  <header class="site-header">
    <div class="brand"><span class="brand-dot"></span>Meadowlark Travel Co.</div>
    <nav class="main-nav">
      <a href="#">Home</a><a href="#">Brimwell Vacations</a><a href="#">Family Trips</a><a href="#">Texas Road Trips</a><a href="#">Other Destinations</a><a href="#">About Us</a><a href="#">Contact</a>
    </nav>
  </header>

  <h1 class="headline">Plan Your <em>Perfect Family</em> Adventure</h1>
  <p class="tagline">Brimwell<span class="sep">•</span>Family Trips<span class="sep">•</span>Road Trips<span class="sep">•</span>Worldwide Destinations</p>

  <section class="cards">
    <article class="card">
      <div class="card-photo p1" role="img" aria-label="Couple in hats looking out over a harbor"></div>
      <h2 class="card-title">Brimwell Vacations<br>Land and Sea</h2>
      <p class="card-text">Magical Brimwell trips planned for families.</p>
      <div class="tags"><span class="tag">Family</span><span class="tag">Theme Parks</span><span class="tag">Luxury</span></div>
    </article>
    <article class="card">
      <div class="card-photo p2" role="img" aria-label="Family reading a map on a city street"></div>
      <h2 class="card-title">Family<br>Trips</h2>
      <p class="card-text">Relaxing vacations for all ages.</p>
      <div class="tags"><span class="tag">Beaches</span><span class="tag">Resorts</span><span class="tag">Relax</span></div>
    </article>
    <article class="card">
      <div class="card-photo p3" role="img" aria-label="Friends enjoying a road trip beside a camper van"></div>
      <h2 class="card-title">Texas Road Trips<br>(East Texas Van Rentals)</h2>
      <p class="card-text">Explore Texas with flexible road adventures.</p>
      <div class="tags"><span class="tag">Adventure</span><span class="tag">Road Trip</span><span class="tag">Van Travel</span></div>
    </article>
    <article class="card">
      <div class="card-photo p4" role="img" aria-label="Aerial view of a beach house in a tropical forest"></div>
      <h2 class="card-title">Other<br>Destinations</h2>
      <p class="card-text">Explore amazing destinations worldwide.</p>
      <div class="tags"><span class="tag">Global</span><span class="tag">Explore</span><span class="tag">Custom</span></div>
    </article>
  </section>

  <footer class="contact-bar">
    <div class="contact-item">
      <span class="icon-circle"><svg width="16" height="16" viewBox="0 0 24 24"><path fill="#fff" d="M6.6 10.8a15 15 0 0 0 6.6 6.6l2.2-2.2c.3-.3.7-.4 1-.2 1.1.4 2.3.6 3.6.6.6 0 1 .4 1 1V20c0 .6-.4 1-1 1A17 17 0 0 1 3 4c0-.6.4-1 1-1h3.5c.6 0 1 .4 1 1 0 1.3.2 2.5.6 3.6.1.3 0 .7-.2 1z"/></svg></span>
      <div><div class="contact-label">Call Us:</div><div class="contact-value">555.010.2040</div></div>
    </div>
    <div class="contact-item" style="margin-left:70px">
      <span class="icon-circle"><svg width="16" height="12" viewBox="0 0 16 12"><rect width="16" height="12" rx="1.5" fill="#fff"/><path d="M1 1.5l7 5 7-5" stroke="#c4954a" stroke-width="1.4" fill="none"/></svg></span>
      <div><div class="contact-label">Email Address:</div><div class="contact-value">hello@meadowlarktravel.example</div></div>
    </div>
    <div class="contact-item" style="margin-left:64px;gap:8px">
      <span class="icon-circle small"></span><a class="social" href="#">Friendbook</a>
    </div>
    <div class="contact-item" style="margin-left:42px;gap:8px">
      <span class="icon-circle small"></span><a class="social" href="#">Snapgram</a>
    </div>
  </footer>
</body>
</html>
```